Looking for a cool & simple business-card-design for digital agency

Hi!

We are a web agency that offers Reputation Management, Vextor & Seo Services and software development. We like cool things, we like innovative styles.

We have uploaded our logo.

Project Deadline Extended Reason: Client does not want any designs with the colorful logo. Please send us submissions ONLY with the blac and white logo. What the client would like to see:1) Back of the card: is a silver logo on a black background2) front of the card with all the data, please use white background and black logo thank you Added Friday, May 8, 2015

Industry/Entity Type

Software

```html
<!DOCTYPE html>
<html lang="en">
<head>
<meta charset="utf-8">
<title>Nexbyte Business Card</title>
<link rel="stylesheet" href="https://fonts.googleapis.com/css2?family=PT+Sans:wght@400;700&display=swap">
<style>
  :root {
    --canvas-bg: #1c1c1c;
    --card-white: #f4f4f4;
    --card-black: #222222;
    --ink: #1a1a1a;
    --ink-soft: #333333;
    --divider: #8a8a8a;
    --silver: #b9b9b9;
  }
  * { margin: 0; padding: 0; box-sizing: border-box; }
  html, body { width: 1200px; height: 1000px; overflow: hidden; }
  body {
    position: relative;
    background: var(--canvas-bg);
    font-family: "PT Sans", sans-serif;
    color: var(--ink);
  }
  .card {
    position: absolute;
    width: 500px;
    height: 278px;
    border-radius: 14px;
  }
  .card--front { left: 270px; top: 199px; background: var(--card-white); }
  .card--back { left: 432px; top: 545px; background: var(--card-black); }

  .brand {
    position: absolute;
    display: flex;
    align-items: center;
    gap: 8px;
    font-family: "PT Sans", sans-serif;
    font-weight: 700;
    font-size: 28px;
    line-height: 1;
  }
  .brand__mark { width: 22px; height: 22px; }
  .card--front .brand { right: 38px; top: 50px; color: var(--ink); }
  .card--front .brand__mark { background: var(--ink); }
  .card--back .brand { right: 42px; top: 192px; color: var(--silver); }
  .card--back .brand__mark { background: var(--silver); }

  .person {
    position: absolute;
    right: 306px;
    top: 154px;
    text-align: right;
  }
  .person__name { font-weight: 700; font-size: 16px; letter-spacing: 0.3px; line-height: 18px; }
  .person__role { font-size: 12px; color: var(--ink-soft); line-height: 15px; }

  .divider {
    position: absolute;
    left: 213px;
    top: 156px;
    width: 1px;
    height: 82px;
    background: var(--divider);
  }

  .contact {
    position: absolute;
    left: 231px;
    top: 153px;
    list-style: none;
    font-size: 12px;
    color: var(--ink-soft);
  }
  .contact__item { display: flex; align-items: center; gap: 5px; height: 14.5px; }
  .contact__icon { width: 10px; height: 10px; flex: none; }
  .address {
    position: absolute;
    left: 231px;
    top: 216px;
    font-size: 12px;
    font-style: normal;
    line-height: 14.5px;
    color: var(--ink-soft);
  }
</style>
</head>
<body>

<section class="card card--front">
  <div class="brand"><span class="brand__mark"></span>Nexbyte</div>

  <div class="person">
    <p class="person__name">JONAS KELLER</p>
    <p class="person__role">Managing Director</p>
  </div>

  <span class="divider"></span>

  <ul class="contact">
    <li class="contact__item">
      <svg class="contact__icon" viewBox="0 0 10 10"><rect width="10" height="10" rx="2" fill="#1a1a1a"/><path d="M3 2.5l1 .2.4 1.4-.7.6a4 4 0 0 0 1.6 1.6l.6-.7 1.4.4.2 1c-.6.6-1.8.6-3-.4S2.4 3.1 3 2.5z" fill="#fff"/></svg>
      +49-(40)-55510-2040
    </li>
    <li class="contact__item">
      <svg class="contact__icon" viewBox="0 0 10 10"><rect width="10" height="10" rx="2" fill="#1a1a1a"/><rect x="2" y="4" width="6" height="3.5" fill="#fff"/><rect x="3" y="2.3" width="4" height="1.4" fill="#fff"/></svg>
      +49-(40)-55510-2040
    </li>
    <li class="contact__item">
      <svg class="contact__icon" viewBox="0 0 10 10"><rect width="10" height="10" rx="2" fill="#1a1a1a"/><rect x="2" y="3" width="6" height="4" fill="none" stroke="#fff" stroke-width="0.8"/><path d="M2 3l3 2.2L8 3" fill="none" stroke="#fff" stroke-width="0.8"/></svg>
      jonas@nexbyteag.de
    </li>
    <li class="contact__item">
      <svg class="contact__icon" viewBox="0 0 10 10"><rect width="10" height="10" rx="2" fill="#1a1a1a"/><circle cx="5" cy="5" r="2.8" fill="none" stroke="#fff" stroke-width="0.8"/><path d="M2.2 5h5.6M5 2.2v5.6" stroke="#fff" stroke-width="0.6"/></svg>
      www.nexbyteag.de
    </li>
  </ul>

  <address class="address">
    Birkenweg 128<br>
    20095 Hamburg, Germany
  </address>
</section>

<section class="card card--back">
  <div class="brand"><span class="brand__mark"></span>Nexbyte</div>
</section>

</body>
</html>
```